BrivoTerna. Lantern of the Steady Harvest. Business card

Professional business card for BrivoTerna (Lantern of the Steady Harvest)
My rationale: Strategy-> Execution-> Results-> Value that lead to the BrivoTerna name: We put the Lantern of the Steady Harvest.
We deliver value to our customers helping them at defining a good strategy (cyan arrow). 90% of well formulated strategies fail due to poor execution so we also consider strategical execution very important (green arrow). Due to the execution we obtain the results (blue arrow). Finally, the results provide feedback to redefine strategy, and the new strategy has to be executed and new results obtained providing new feedback and on and on. It's like a wheel that finally, must create corporate value: value for shareholders, staholders, employees, providers...-

Target Market(s)

CEOs and steering comitees , invewrnent funds

Industry/Entity Type

Business Consultant

Contact Information for Business Card

Teodoro Vinsquel
CEO & Founder
teodoro.vinsquel@brivoterna-example.com
Mobile: +34 655.803.912
www.brivoterna-example.com

Colors

Designer to choose colors to be used in the design.

Requirements
Nice to have
• Nice to hace the words: Strategy, execution, results
• Nice to vave the claim: Lantern of the Steady Harvest
• The three colors should be shown:
• cyan for STRATEGY
• green for EXECUTION
• blue for RESULTS
Should not have
• Complete black background

```html
<!DOCTYPE html>
<html lang="en">
<head>
<meta charset="utf-8">
<title>BrivoTerna – Business Card</title>
<link rel="stylesheet" href="https://fonts.googleapis.com/css2?family=Open+Sans:wght@400;600;700;800&display=swap">
<style>
  :root {
    --navy: #0b3aa8;
    --navy-deep: #0a2f8f;
    --cyan: #00aeef;
    --white: #ffffff;
    --ink: #1b1b1b;
    --stage: #d9dde3;
  }
  * { box-sizing: border-box; margin: 0; padding: 0; }
  html, body { width: 1200px; height: 900px; overflow: hidden; }
  body {
    background: var(--stage);
    font-family: "Open Sans", sans-serif;
    position: relative;
  }
  .card {
    position: absolute;
    width: 680px;
    height: 390px;
    border-radius: 18px;
    overflow: hidden;
    box-shadow: 0 10px 30px rgba(0,0,0,0.18);
  }
  .card-front { left: 60px; top: 50px; background: var(--white); }
  .card-back { left: 460px; top: 460px; background: var(--navy); }

  .front-band {
    position: absolute; left: 0; right: 0; top: 215px; bottom: 0;
    background: var(--cyan);
  }
  .brand-name {
    position: absolute; left: 0; right: 0;
    text-align: center;
    font-weight: 800;
    letter-spacing: -0.5px;
  }
  .card-front .brand-name { top: 62px; font-size: 46px; color: var(--navy); }
  .person-name {
    position: absolute; left: 0; right: 0; top: 138px;
    text-align: center; font-size: 21px; font-weight: 800;
    color: var(--navy); letter-spacing: 0.5px;
  }
  .person-role {
    position: absolute; left: 0; right: 0; top: 168px;
    text-align: center; font-size: 13px; color: var(--ink);
  }
  .contacts {
    position: absolute; left: 0; right: 0; top: 238px;
    display: flex; justify-content: center; gap: 22px;
    color: var(--white); font-size: 14px;
  }
  .contact-column { display: flex; flex-direction: column; gap: 6px; }
  .contact-item { display: flex; align-items: center; gap: 6px; white-space: nowrap; }
  .contact-item svg { width: 13px; height: 13px; flex: none; }

  .edge-shape { position: absolute; left: 0; bottom: 0; width: 680px; height: 70px; }
  .pillars {
    position: absolute; left: 225px; right: 0; bottom: 10px; height: 30px;
    display: flex; align-items: center; justify-content: center; gap: 14px;
    color: var(--white); font-weight: 800; font-size: 15px; letter-spacing: 0.5px;
  }

  .card-back .brand-name { top: 145px; font-size: 66px; color: var(--white); }
  .claim {
    position: absolute; left: 175px; width: 390px; bottom: 14px;
    text-align: center; color: var(--navy);
    font-size: 15px; font-weight: 600; letter-spacing: 0.6px;
    text-transform: uppercase;
  }
</style>
</head>
<body>

<section class="card card-front" aria-label="Card front">
  <div class="front-band"></div>
  <div class="brand-name">BrivoTerna</div>
  <div class="person-name">TEODORO VINSQUEL</div>
  <div class="person-role">CEO &amp; Founder</div>

  <div class="contacts">
    <div class="contact-column">
      <div class="contact-item">
        <svg viewBox="0 0 16 16" fill="none" stroke="#fff" stroke-width="1.4"><circle cx="8" cy="8" r="7"/><path d="M5.5 4.5l1.5 1.6-.8 1.2c.6 1.2 1.4 2 2.5 2.5l1.2-.8 1.6 1.5-1 1.2C7.6 11.5 4.5 8.4 4.3 5.5z" fill="#fff" stroke="none"/></svg>
        <span>+34 655.803.912</span>
      </div>
    </div>
    <div class="contact-column">
      <div class="contact-item">
        <svg viewBox="0 0 16 16"><rect x="1" y="3" width="14" height="10" rx="1" fill="#fff"/><path d="M1.5 3.5L8 9l6.5-5.5" fill="none" stroke="#00aeef" stroke-width="1.3"/></svg>
        <span>teodoro.vinsquel@brivoterna-example.com</span>
      </div>
      <div class="contact-item">
        <svg viewBox="0 0 16 16" fill="none" stroke="#fff" stroke-width="1.3"><circle cx="8" cy="8" r="6.5"/><ellipse cx="8" cy="8" rx="3" ry="6.5"/><path d="M1.5 8h13"/></svg>
        <span>www.brivoterna-example.com</span>
      </div>
    </div>
  </div>

  <svg class="edge-shape" viewBox="0 320 680 70" aria-hidden="true">
    <path d="M0 390 V378 H190 C212 378 203 348 228 348 H680 V390 Z" fill="var(--navy-deep)"/>
  </svg>
  <div class="pillars">
    <span>STRATEGY</span><span>-</span><span>EXECUTION</span><span>-</span><span>RESULTS</span>
  </div>
</section>

<section class="card card-back" aria-label="Card back">
  <div class="brand-name">BrivoTerna</div>
  <svg class="edge-shape" viewBox="0 320 680 70" aria-hidden="true">
    <path d="M0 390 V372 H140 C162 372 152 342 178 342 H555 C580 342 572 326 598 326 H680 V390 Z" fill="var(--white)"/>
  </svg>
  <div class="claim">Lantern of the Steady Harvest</div>
</section>

</body>
</html>
```